New stationary design for online film company

We need some new stationary to fit with our new logo. The stationary should be professional, clean and simple.
We need designs for a full set of business stationary.
We need - letterhead, envelopes, invoices, proposals, coverslip/note and cover page

Industry/Entity Type

Business

```html
<!DOCTYPE html>
<html lang="en">
<head>
<meta charset="utf-8">
<title>reelwavetv stationery set</title>
<link href="https://fonts.googleapis.com/css2?family=Open+Sans:wght@400;600;700&display=swap" rel="stylesheet">
<style>
  :root {
    --navy: #0b4470;
    --sky: #6aa3c1;
    --paper: #ffffff;
    --ghost: #e6eaf0;
    --ink: #333c44;
    --backdrop: #e4e6e9;
    --outline: #5a6068;
  }
  * { box-sizing: border-box; margin: 0; padding: 0; }
  html, body { width: 1200px; height: 761px; overflow: hidden; }
  body {
    background: var(--backdrop);
    font-family: "Open Sans", sans-serif;
    color: var(--ink);
    position: relative;
  }
  .sheet { position: absolute; background: var(--paper); overflow: hidden; box-shadow: 0 2px 8px rgba(0,0,0,.18); }
  .brand { display: flex; align-items: center; gap: 8px; color: var(--navy); font-weight: 600; letter-spacing: -0.5px; line-height: 1; white-space: nowrap; }
  .brand-dot { border-radius: 50%; background: var(--navy); flex: none; }
  .wave { position: absolute; left: 0; bottom: 0; width: 100%; }
  .contact { position: absolute; color: #fff; text-align: right; line-height: 1.6; white-space: nowrap; }

  /* letterhead */
  .letterhead { left: 18px; top: 22px; width: 507px; height: 718px; }
  .letterhead .brand { position: absolute; left: 138px; top: 36px; font-size: 38px; }
  .letterhead .brand-dot { width: 36px; height: 36px; }
  .watermark { position: absolute; left: 122px; top: 282px; width: 264px; height: 264px; border-radius: 50%; border: 24px solid var(--ghost); }
  .letterhead .contact { right: 10px; bottom: 9px; font-size: 6.5px; }
  .letterhead .contact .address { margin-top: 6px; }

  /* business cards */
  .card-front { left: 570px; top: 20px; width: 216px; height: 122px; background: var(--navy); }
  .card-front .brand-dot { position: absolute; left: 79px; top: 24px; width: 58px; height: 58px; background: none; border: 7px solid #fff; }
  .card-front .web { position: absolute; left: 0; right: 0; bottom: 9px; text-align: center; color: #fff; font-size: 5.5px; letter-spacing: 1.6px; }
  .card-back { left: 798px; top: 23px; width: 216px; height: 123px; }
  .card-back .brand { position: absolute; left: 12px; top: 14px; font-size: 19px; gap: 5px; }
  .card-back .brand-dot { width: 18px; height: 18px; }
  .holder { position: absolute; left: 12px; top: 62px; line-height: 1.25; }
  .holder-name { font-size: 7.5px; font-weight: 700; color: var(--navy); }
  .holder-role { font-size: 6px; color: var(--sky); }
  .card-back .contact { right: 7px; bottom: 6px; font-size: 5px; }
  .card-back .contact .address { margin-top: 4px; }

  /* envelopes */
  .envelope-flaps { position: absolute; left: 570px; top: 166px; width: 582px; height: 191px; }
  .envelope-open { position: absolute; left: 558px; top: 357px; width: 583px; height: 261px; background: var(--paper); border: 1px solid var(--outline); }
  .envelope-open .flap-line { position: absolute; left: 0; top: 0; }
  .envelope-open .brand-dot { position: absolute; left: 270px; top: 26px; width: 42px; height: 42px; }
  .envelope-front { left: 594px; top: 470px; width: 584px; height: 260px; border: 1px solid #9aa0a6; }
  .envelope-front .brand { position: absolute; left: 20px; top: 20px; font-size: 26px; gap: 6px; }
  .envelope-front .brand-dot { width: 26px; height: 26px; }
  .return-address { position: absolute; left: 20px; top: 70px; font-size: 8.5px; letter-spacing: .8px; color: #222; }
  .envelope-front .web { position: absolute; right: 28px; bottom: 20px; color: #fff; font-size: 7.5px; letter-spacing: 2px; }
</style>
</head>
<body>

  <section class="sheet letterhead">
    <div class="brand"><span class="brand-dot"></span>reelwavetv</div>
    <div class="watermark" role="img" aria-label="Faint brand circle"></div>
    <svg class="wave" viewBox="0 0 507 90" height="90" preserveAspectRatio="none" aria-hidden="true">
      <path d="M0 74 C140 72 300 22 507 12 L507 20 C300 30 160 76 0 80Z" fill="var(--sky)"/>
      <path d="M0 70 C140 66 230 50 280 46 C200 58 120 70 0 74Z" fill="var(--navy)"/>
      <path d="M0 84 C150 82 310 34 507 26 L507 90 L0 90Z" fill="var(--navy)"/>
    </svg>
    <div class="contact">
      <div>&#9742; 123-456-7890</div>
      <div>&#9993; info@reelwavetv.com</div>
      <div>&#9673; www.reelwavetv.com</div>
      <div class="address">00, Complex Name, street, city 000452</div>
    </div>
  </section>

  <section class="sheet card-front">
    <span class="brand-dot"></span>
    <div class="web">www.reelwavetv.com</div>
  </section>

  <section class="sheet card-back">
    <div class="brand"><span class="brand-dot"></span>reelwavetv</div>
    <div class="holder">
      <div class="holder-name">Your Name</div>
      <div class="holder-role">Designation</div>
    </div>
    <svg class="wave" viewBox="0 0 216 80" height="80" preserveAspectRatio="none" aria-hidden="true">
      <path d="M0 52 C70 52 120 10 216 2 L216 6 C122 14 74 56 0 56Z" fill="var(--sky)"/>
      <path d="M0 58 C50 57 80 52 104 46 C80 56 50 62 0 62Z" fill="var(--navy)"/>
      <path d="M0 66 C75 64 122 16 216 9 L216 80 L0 80Z" fill="var(--navy)"/>
    </svg>
    <div class="contact">
      <div>&#9742; 123-456-7890</div>
      <div>&#9647; 123-456-7890</div>
      <div>&#9993; info@reelwavetv.com</div>
      <div>&#9673; www.reelwavetv.com</div>
      <div class="address">00, Complex Name, street, city 000452</div>
    </div>
  </section>

  <svg class="envelope-flaps" viewBox="0 0 582 191" aria-hidden="true">
    <rect x="0" y="0" width="582" height="191" fill="var(--paper)"/>
    <path d="M0 0 H582 L572 38 C568 52 556 58 540 62 L420 78 H162 L42 62 C26 58 14 52 10 38Z" fill="var(--sky)"/>
    <path d="M0 78 H582 L572 118 C568 130 556 134 540 138 L316 180 C302 182 280 182 266 180 L42 138 C26 134 14 130 10 118Z" fill="var(--navy)"/>
    <circle cx="291" cy="42" r="18" fill="none" stroke="#fff" stroke-width="5"/>
    <circle cx="291" cy="133" r="18" fill="none" stroke="#fff" stroke-width="5"/>
  </svg>

  <section class="envelope-open">
    <svg class="flap-line" viewBox="0 0 583 261" width="583" height="261" aria-hidden="true">
      <path d="M0 0 L8 26 C12 44 24 52 40 56 L270 100 C282 102 300 102 312 100 L540 56 C556 52 566 44 570 26 L580 0" fill="none" stroke="var(--outline)" stroke-width="1"/>
    </svg>
    <span class="brand-dot"></span>
  </section>

  <section class="sheet envelope-front">
    <div class="brand"><span class="brand-dot"></span>reelwavetv</div>
    <p class="return-address">00, Complex Name, street, city 000452</p>
    <svg class="wave" viewBox="0 0 584 90" height="90" preserveAspectRatio="none" aria-hidden="true">
      <path d="M0 60 C160 58 330 14 584 6 L584 12 C330 20 170 64 0 66Z" fill="var(--sky)"/>
      <path d="M0 56 C120 54 220 46 320 38 C220 54 120 62 0 62Z" fill="var(--navy)"/>
      <path d="M0 72 C170 70 340 20 584 14 L584 90 L0 90Z" fill="var(--navy)"/>
    </svg>
    <div class="web">www.reelwavetv.com</div>
  </section>

</body>
</html>
```